Brightfield Ventures Inc. Letterhead

Creation of attractive and eye catching letterhead for a business start-up for the construction industry. Letterhead must relate to construction, but avoid standard hammer and tools in the design.

I forgot to add some details, sorry about that. Some pertinent info: Ph: 916-555-0187 brightfieldventures.example 448 Willowmere Ave, Ste 210 Folsom, CA 95999 info@brightfieldventures.example not sure if slogan should be in there" “Connecting construction professionals to create a purpose driven industry.” must be able to be used in word. Thanks!

```html
<!DOCTYPE html>
<html lang="en">
<head>
<meta charset="utf-8">
<title>Brightfield Ventures Inc. Letterhead</title>
<link href="https://fonts.googleapis.com/css2?family=Open+Sans:wght@400;600;700&family=Montserrat:wght@600;700&display=swap" rel="stylesheet">
<style>
  :root {
    --navy: #0f1d5a;
    --red: #c4161c;
    --ink: #3a3a3a;
    --muted: #666;
    --paper: #ffffff;
    --backdrop: #e9eaec;
  }
  * { box-sizing: border-box; margin: 0; padding: 0; }
  html, body {
    width: 1200px; height: 784px; overflow: hidden;
    background: var(--backdrop);
    font-family: "Open Sans", Arial, sans-serif;
  }
  .letterhead {
    position: absolute; left: 330px; top: 22px;
    width: 540px; height: 740px;
    background: var(--paper);
    box-shadow: 0 2px 10px rgba(0,0,0,.12);
    overflow: hidden;
  }
  .brand {
    position: absolute; left: 44px; top: 44px;
    display: flex; align-items: center; gap: 7px;
  }
  .brand-mark { width: 14px; height: 14px; background: var(--red); }
  .brand-name {
    font-family: "Montserrat", Arial, sans-serif; font-weight: 700;
    font-size: 13px; letter-spacing: 1.2px; color: var(--navy);
    text-transform: uppercase;
  }
  .header-info {
    position: absolute; right: 44px; top: 40px;
    display: flex; gap: 10px; font-size: 6.5px; line-height: 1.55; color: var(--muted);
  }
  .address { text-align: left; }
  .address .company { color: var(--red); font-weight: 700; font-size: 7px; }
  .divider { width: 1px; background: #bbb; }
  .contact-row { display: flex; align-items: center; gap: 4px; }
  .contact-row svg { width: 7px; height: 7px; fill: var(--red); }
  .letter-body {
    position: absolute; left: 44px; top: 128px; width: 452px;
    font-size: 10.2px; line-height: 1.45; color: var(--ink);
  }
  .salutation { font-weight: 700; font-size: 12px; color: #333; margin-bottom: 10px; }
  .letter-body p { margin-bottom: 14px; }
  .signature {
    width: 120px; height: 46px; margin-top: 8px;
    background: linear-gradient(90deg, #f1f1f1, #e2e2e2);
    border-radius: 2px;
  }
  .footer-wave { position: absolute; left: 0; bottom: 0; width: 540px; height: 150px; }
</style>
</head>
<body>
  <main class="letterhead">
    <div class="brand">
      <span class="brand-mark"></span>
      <span class="brand-name">Brightfield Ventures</span>
    </div>

    <div class="header-info">
      <div class="address">
        <div class="company">Brightfield Ventures Inc.</div>
        <div>448 Willowmere Ave, Ste 210,</div>
        <div>Folsom, CA 95999</div>
      </div>
      <div class="divider"></div>
      <div class="contacts">
        <div class="contact-row">
          <svg viewBox="0 0 10 10"><path d="M2 0.5 L3.6 0.5 L4.3 2.8 L3.2 3.6 Q4.2 5.8 6.4 6.8 L7.2 5.7 L9.5 6.4 L9.5 8 Q9.5 9.5 8 9.5 Q0.5 9 0.5 2 Q0.5 0.5 2 0.5Z"/></svg>
          <span>916-555-0187</span>
        </div>
        <div class="contact-row">
          <svg viewBox="0 0 10 10"><path d="M0.5 2 H9.5 V8.5 H0.5Z M0.5 2 L5 5.5 L9.5 2" fill="none" stroke="#c4161c" stroke-width="1.2"/></svg>
          <span>info@brightfieldventures.example</span>
        </div>
        <div class="contact-row">
          <svg viewBox="0 0 10 10"><circle cx="5" cy="5" r="4.3" fill="none" stroke="#c4161c" stroke-width="1.1"/><path d="M0.7 5 H9.3 M5 0.7 Q2.5 5 5 9.3 M5 0.7 Q7.5 5 5 9.3" fill="none" stroke="#c4161c" stroke-width="0.8"/></svg>
          <span>brightfieldventures.example</span>
        </div>
      </div>
    </div>

    <section class="letter-body">
      <div class="salutation">Dear Mr. John,</div>
      <p>Lorem Ipsum is simply dummy text of the printing and typesetting industry. Lorem Ipsum has been the industry's standard dummy text ever since the 1500s, when an unknown printer took a galley of type and scrambled it to make a type specimen book. It has survived not only five centuries, but also the leap into electronic typesetting, remaining essentially unchanged.</p>
      <p>The standard chunk of Lorem Ipsum used since the 1500s is reproduced below for those interested. Sections 1.10.32 and 1.10.33 from "de Finibus Bonorum et Malorum" by Cicero are also reproduced in their exact original form, accompanied by English versions from the 1914 translation by H. Rackham.</p>
      <p>Lorem Ipsum is simply dummy text of the printing and typesetting industry. Lorem Ipsum has been the industry's standard dummy text ever since the 1500s, when an unknown printer took a galley of type and scrambled it to make a type specimen book. It has survived not only five centuries, but also the leap into electronic typesetting, remaining essentially unchanged. It was popularised in the</p>
      <p>Lorem Ipsum is simply dummy text of the printing and typesetting industry. Lorem Ipsum has been the industry's standard dummy text ever since the 1500s, when an unknown printer took a galley of type and scrambled it to make a type specimen book. It has survived not only five centuries, but also the leap into electronic typesetting, remaining essentially unchanged. It was popularised in the</p>
      <p>Lorem Ipsum is simply dummy text of the printing and typesetting industry. Lorem Ipsum has been the industry's standard dummy text ever since the 1500s, when an unknown printer took a galley of type and scrambled it to make a type specimen book.</p>
      <div class="signature" role="img" aria-label="Handwritten signature of the sender"></div>
    </section>

    <svg class="footer-wave" viewBox="0 0 540 150" preserveAspectRatio="none" aria-hidden="true">
      <path d="M0 150 C120 140 220 110 300 70 C380 30 460 10 540 4 L540 150 Z" fill="var(--red)"/>
      <path d="M0 150 C130 146 230 120 310 82 C390 44 470 24 540 18 L540 150 Z" fill="var(--paper)"/>
      <path d="M0 150 C140 150 240 128 320 92 C400 56 475 36 540 30 L540 150 Z" fill="var(--navy)"/>
    </svg>
  </main>
</body>
</html>
```